NZ First of it's kind solutions directory and marketplace for busy Mums needs a business card design

We need a business card design for our new nationwide business in NZ (long term plans to go global). We provide solutions to the everyday challenges that busy Mums face by connecting them with quality communities and suppliers of carefully selected, relevant products and services. We sell direct via our online marketplace. The final design should communicate our values of inclusivity, quality and smart solutions. Colours should incorporate our logo colour palette of #477077 and #6ba8b2. Our website is at https://www.brightnestmums.example

Target Market(s)

busy Mums, Age 28 – 50, female, income over $100K, location main centres NZ primarily but NZ wide. Is likely juggling work or career with a young family. Probably had hobbies which have fallen by the wayside.
-Wants to succeed in her chosen career without compromising on family life
-to successfully juggle her career without feeling like she is compromising her children
- Is time poor, something always has to give and it’s generally her health (she’ll stay up late, get stressed)
- probably ex corporate or professional career. Has discretional income

Industry/Entity Type

Business

Contact Information for Business Card

Lena Forbisher, Founder, BrightNestMums.example (Strapline Tap; Gather; Sorted), 47 Kowhai Terrace, Ellerslie, Auckland 1051, New Zealand. Mob: 021 483 517 Ph: +64 (0)9 571 4860

Font styles to use
Other font styles liked:
• Raleway, and/or Architects Daughter

Colors
00a990
33b8a4
86cfc6
cfeae6

Requirements
Must have
• the above details, streamline. the logo and colours associated with those logos
Should not have
• foil or metallic colours

```html
<!DOCTYPE html>
<html lang="en">
<head>
<meta charset="utf-8">
<title>BrightNestMums — Business Card</title>
<link rel="stylesheet" href="https://fonts.googleapis.com/css2?family=Roboto:wght@500;700&family=Roboto+Condensed:ital,wght@0,400;1,400&display=swap">
<style>
  :root {
    --brand-deep: #477077;
    --brand-light: #6ba8b2;
    --ink: #3b3f42;
    --ink-soft: #4a4e52;
    --backdrop: #dedede;
    --card: #fbfbfb;
    --card-edge: #f0f0f0;
  }
  * { margin: 0; padding: 0; box-sizing: border-box; }
  html, body {
    width: 1200px; height: 576px; overflow: hidden;
    background: var(--backdrop);
  }
  .canvas { position: relative; width: 1200px; height: 576px; }

  .card {
    position: absolute; top: 138px;
    width: 484px; height: 294px;
    border-radius: 14px;
    background: linear-gradient(180deg, var(--card) 0%, var(--card-edge) 100%);
  }
  .card--front { left: 82px; }
  .card--back { left: 602px; width: 481px; }

  .wordmark {
    position: absolute;
    font-family: "Roboto", sans-serif;
    font-weight: 500;
    color: var(--brand-deep);
    letter-spacing: -0.5px;
    white-space: nowrap;
    transform: translateX(-50%);
  }
  .strapline {
    position: absolute;
    font-family: "Roboto", sans-serif;
    font-weight: 500;
    color: var(--ink);
    text-transform: uppercase;
    white-space: nowrap;
    transform: translateX(-50%);
  }
  .strapline .divider { color: var(--brand-light); margin: 0 0.6em; }

  .card--front .wordmark { left: 242px; top: 120px; font-size: 36px; }
  .card--front .strapline { left: 242px; top: 170px; font-size: 11px; letter-spacing: 3.4px; }

  .card--back .wordmark { left: 132px; top: 168px; font-size: 26px; }
  .card--back .strapline { left: 132px; top: 206px; font-size: 9px; letter-spacing: 2.8px; }

  .details {
    position: absolute; left: 264px; top: 56px;
    font-family: "Roboto Condensed", sans-serif;
    color: var(--ink-soft);
  }
  .details__name {
    font-family: "Roboto", sans-serif;
    font-weight: 700;
    font-size: 20px;
    color: var(--brand-deep);
    line-height: 24px;
  }
  .details__role { font-style: italic; font-size: 12.5px; line-height: 18px; }
  .details__address { margin-top: 16px; font-size: 13px; line-height: 18px; }
  .details__contacts { list-style: none; margin-top: 9px; }
  .details__contacts li {
    display: flex; align-items: center;
    font-size: 13px; line-height: 18.4px;
  }
  .details__contacts svg {
    width: 11px; height: 11px; margin-right: 9px; flex: none;
    fill: var(--brand-light);
  }
</style>
</head>
<body>
<main class="canvas">

  <section class="card card--front" aria-label="Business card front">
    <div class="wordmark">BrightNestMums</div>
    <div class="strapline">Tap<span class="divider">|</span>Gather<span class="divider">|</span>Sorted</div>
  </section>

  <section class="card card--back" aria-label="Business card back">
    <div class="wordmark">BrightNestMums</div>
    <div class="strapline">Tap<span class="divider">|</span>Gather<span class="divider">|</span>Sorted</div>

    <div class="details">
      <p class="details__name">Lena Forbisher</p>
      <p class="details__role">Founder</p>
      <p class="details__address">47 Kowhai Terrace, Ellerslie,<br>Auckland 1051, New Zealand</p>
      <ul class="details__contacts">
        <li>
          <svg viewBox="0 0 12 12" aria-hidden="true"><rect x="3" y="0.5" width="6" height="11" rx="1.2"/><rect x="4" y="2" width="4" height="7" fill="#fbfbfb"/></svg>
          021 483 517
        </li>
        <li>
          <svg viewBox="0 0 12 12" aria-hidden="true"><path d="M1 4.2C1 2.5 3.5 1.5 6 1.5s5 1 5 2.7V5H8.5V3.8h-5V5H1z"/><path d="M2.5 6h7l1 5h-9z"/><circle cx="6" cy="8.3" r="1.2" fill="#fbfbfb"/></svg>
          +64 (0)9 571 4860
        </li>
        <li>
          <svg viewBox="0 0 12 12" aria-hidden="true"><rect x="0.5" y="2.5" width="11" height="7.5" rx="0.6"/><path d="M1 3l5 4 5-4" fill="none" stroke="#fbfbfb" stroke-width="1"/></svg>
          www.BrightNestMums.example
        </li>
        <li>
          <svg viewBox="0 0 12 12" aria-hidden="true"><circle cx="6" cy="6" r="5.5"/><g fill="none" stroke="#fbfbfb" stroke-width="0.8"><ellipse cx="6" cy="6" rx="2.3" ry="5.5"/><path d="M0.5 6h11M1.5 3.3h9M1.5 8.7h9"/></g></svg>
          lena@brightnestmums.example
        </li>
      </ul>
    </div>
  </section>

</main>
</body>
</html>
```